Business Card Design

New business card design

Target Market(s)

Residential & Commercial Property Managers

Industry/Entity Type

Plumbing Services

Contact Information for Business Card

Name - Rowan Keddle, title - Director, Phone Number - 0431 286 517, email - rowan@tbk-plumbing.com.au, Company ABN - 73 215 904 386,

Font styles to use
Sans Serif

Colors
0054AA
0677BA
7BADD7
CADEEF
E8F1F8

```html
<!DOCTYPE html>
<html lang="en">
<head>
<meta charset="utf-8">
<title>TBK Plumbing Services – Business Card</title>
<link rel="stylesheet" href="https://fonts.googleapis.com/css2?family=Montserrat:wght@300;400;700&display=swap">
<style>
  :root{
    --stage:#3a3a3a;
    --card:#1e232a;
    --blue:#00aeef;
    --white:#ffffff;
  }
  *{margin:0;padding:0;box-sizing:border-box}
  html,body{width:1200px;height:895px;overflow:hidden}
  body{
    background:var(--stage);
    font-family:"Montserrat",sans-serif;
    display:flex;flex-direction:column;align-items:center;justify-content:center;gap:46px;
  }
  .card{
    position:relative;width:640px;height:366px;border-radius:26px;
    background:var(--card);overflow:hidden;color:var(--white);
  }
  .wordmark{position:absolute;display:flex;align-items:center;gap:14px;font-weight:300;color:var(--white)}
  .wordmark__dot{width:22px;height:22px;border-radius:50%;background:var(--blue);flex:none}
  .wordmark__text{display:flex;flex-direction:column;line-height:1}
  .wordmark__name{font-size:84px;letter-spacing:2px}
  .wordmark__tagline{font-size:13px;letter-spacing:9px;margin-top:10px;padding-left:4px}
  .card--back .wordmark{left:50%;top:50%;transform:translate(-50%,-50%)}
  .card--front .wordmark{left:44px;top:40px}
  .card--front .wordmark__name{font-size:70px}
  .card--front .wordmark__tagline{font-size:11px;letter-spacing:7px}
  .accent-panel{position:absolute;right:0;top:0;width:214px;height:100%;background:var(--white)}
  .accent-panel__fill{position:absolute;left:0;top:28px;right:34px;bottom:0;background:var(--blue);border-radius:0 0 0 0}
  .contact{position:absolute;left:60px;top:186px}
  .contact__name{font-weight:700;font-size:26px;color:var(--blue);line-height:1.1}
  .contact__title{font-weight:400;font-size:17px;margin-top:4px}
  .contact__list{list-style:none;margin-top:14px;font-size:15px;line-height:1.55}
  .contact__item{display:flex;align-items:center;gap:10px}
  .contact__icon{width:16px;height:16px;flex:none}
  .contact__abn{font-size:15px;margin-top:12px}
</style>
</head>
<body>

<section class="card card--back" aria-label="Business card back">
  <div class="wordmark">
    <span class="wordmark__dot"></span>
    <div class="wordmark__text">
      <span class="wordmark__name">tbk</span>
      <span class="wordmark__tagline">plumbing services</span>
    </div>
  </div>
</section>

<section class="card card--front" aria-label="Business card front">
  <div class="accent-panel"><div class="accent-panel__fill"></div></div>

  <div class="wordmark">
    <span class="wordmark__dot"></span>
    <div class="wordmark__text">
      <span class="wordmark__name">tbk</span>
      <span class="wordmark__tagline">plumbing services</span>
    </div>
  </div>

  <div class="contact">
    <p class="contact__name">Rowan Keddle</p>
    <p class="contact__title">Director</p>
    <ul class="contact__list">
      <li class="contact__item">
        <svg class="contact__icon" viewBox="0 0 24 24" aria-hidden="true"><path fill="#00aeef" d="M6.6 10.8a15.1 15.1 0 0 0 6.6 6.6l2.2-2.2c.3-.3.7-.4 1-.2 1.1.4 2.3.6 3.6.6.6 0 1 .4 1 1V20c0 .6-.4 1-1 1A17 17 0 0 1 3 4c0-.6.4-1 1-1h3.5c.6 0 1 .4 1 1 0 1.3.2 2.5.6 3.6.1.3 0 .7-.2 1z"/></svg>
        <span>0431 286 517</span>
      </li>
      <li class="contact__item">
        <svg class="contact__icon" viewBox="0 0 24 24" aria-hidden="true"><rect x="2" y="5" width="20" height="14" rx="1" fill="#00aeef"/><path d="M3 6l9 7 9-7" fill="none" stroke="#1e232a" stroke-width="2"/></svg>
        <span>rowan@tbk-plumbing.com.au</span>
      </li>
    </ul>
    <p class="contact__abn">ABN - 73 215 904 386</p>
  </div>
</section>

</body>
</html>
```